Business Card Design Project - del varosi group

dear Sirs

we need business card design for our group ( DEL Varosi Group ) , i have got the Logo design of our group from pixel harbor in previous , so all need details relating to our group i think available with you, as well as the the chosen logo design

we hope to provide us with business card logo that to be appropaite and satisfactory to us .

thanks

note : logo design of our group is attached .
Updates

Reason: please extend the deadline of my project for additional 15 days because i didn't received appropriate design for our gruop yet . kindly beaware that i have received 77 design till now , supossed to send me 200-250 design at least . thanks

Target Market(s)

contents

name : Kerem EL Nadiri

position : Operation Manager

Industry/Entity Type

Business

Requirements
Must have

• person name

group logo
Nice to have
• logo color matching with back background

```html
<!DOCTYPE html>
<html lang="en">
<head>
<meta charset="utf-8">
<title>DEL Varosi Group – Business Card</title>
<link rel="stylesheet" href="https://fonts.googleapis.com/css2?family=Archivo:ital,wght@0,600;0,700;0,800;1,800&family=Archivo+Narrow:wght@700&display=swap">
<style>
  :root {
    --card-blue: #0636c9;
    --frame-white: #ffffff;
    --name-gold: #c9941c;
    --title-yellow: #f2d25a;
    --detail-gold: #e7bf3c;
    --mark-gold: #d9b23a;
    --emblem-light: #f2df84;
    --emblem-deep: #c9980e;
  }
  html, body {
    margin: 0;
    padding: 0;
    width: 1200px;
    height: 686px;
    overflow: hidden;
    background: var(--card-blue);
  }
  .card {
    position: relative;
    width: 1200px;
    height: 686px;
    background: var(--card-blue);
    overflow: hidden;
    font-family: "Archivo", Arial, sans-serif;
  }
  .emblem-area {
    position: absolute;
    left: 120px;
    top: 0;
  }
  .info-frame {
    position: absolute;
    left: 0;
    top: 0;
  }
  .person-name {
    position: absolute;
    left: 838px;
    top: 150px;
    margin: 0;
    font-weight: 800;
    font-size: 33px;
    letter-spacing: 0.2px;
    color: var(--name-gold);
    white-space: nowrap;
  }
  .person-title {
    position: absolute;
    left: 838px;
    top: 194px;
    margin: 0;
    font-weight: 800;
    font-style: italic;
    font-size: 26px;
    color: var(--title-yellow);
    white-space: nowrap;
  }
  .contact-list {
    position: absolute;
    left: 840px;
    top: 269px;
    margin: 0;
    padding: 0;
    list-style: none;
  }
  .contact-row {
    display: flex;
    align-items: baseline;
    height: 28.8px;
    color: var(--detail-gold);
    white-space: nowrap;
  }
  .contact-label {
    width: 73px;
    font-family: "Archivo Narrow", "Arial Narrow", sans-serif;
    font-weight: 700;
    font-size: 16px;
    font-variant: small-caps;
  }
  .contact-value {
    font-weight: 700;
    font-size: 17px;
    letter-spacing: 0.6px;
  }
  .contact-value.is-small {
    font-size: 15px;
    font-variant: small-caps;
    letter-spacing: 0.8px;
  }
  .group-name {
    position: absolute;
    left: 56px;
    top: 552px;
    display: flex;
    align-items: center;
    gap: 14px;
  }
  .group-name-square {
    width: 28px;
    height: 28px;
    background: var(--mark-gold);
  }
  .group-name-text {
    font-weight: 700;
    font-size: 42px;
    letter-spacing: 1px;
    color: var(--frame-white);
    white-space: nowrap;
  }
</style>
</head>
<body>
  <main class="card">
    <svg class="emblem-area" width="690" height="540" viewBox="0 0 690 540" role="img" aria-label="Large group emblem in gold tones as background decoration">
      <defs>
        <radialGradient id="emblemGlow" cx="50%" cy="50%" r="50%">
          <stop offset="0%" stop-color="var(--emblem-light)" stop-opacity="0.85"/>
          <stop offset="55%" stop-color="var(--emblem-deep)" stop-opacity="0.55"/>
          <stop offset="100%" stop-color="var(--card-blue)" stop-opacity="0"/>
        </radialGradient>
      </defs>
      <ellipse cx="345" cy="270" rx="345" ry="240" fill="url(#emblemGlow)"/>
    </svg>

    <svg class="info-frame" width="1200" height="686" viewBox="0 0 1200 686" aria-hidden="true">
      <rect x="800" y="95" width="389" height="141" fill="var(--frame-white)"/>
      <rect x="800" y="95" width="371" height="362" fill="var(--frame-white)"/>
      <rect x="816" y="114" width="355" height="328" fill="var(--card-blue)"/>
    </svg>

    <h1 class="person-name">KEREM EL NADIRI</h1>
    <p class="person-title">OPERATION MANAGER</p>

    <ul class="contact-list">
      <li class="contact-row"><span class="contact-label">Tel :</span><span class="contact-value">01234-56789-01234</span></li>
      <li class="contact-row"><span class="contact-label">Fax :</span><span class="contact-value">01234-56789-01234</span></li>
      <li class="contact-row"><span class="contact-label">Mobile :</span><span class="contact-value">01234-56789-01234</span></li>
      <li class="contact-row"><span class="contact-label">Email :</span><span class="contact-value is-small">knadiri@delvarosigroup.com</span></li>
      <li class="contact-row"><span class="contact-label">Website :</span><span class="contact-value is-small">www.delvarosigroup.com</span></li>
      <li class="contact-row"><span class="contact-label">PO . Box :</span><span class="contact-value"></span></li>
    </ul>

    <div class="group-name">
      <span class="group-name-square"></span>
      <span class="group-name-text">DEL VAROSI GROUP</span>
    </div>
  </main>
</body>
</html>
```